Local Flower Farm Needs Business Card Design

I need business cards designed for a flower farm based in Eudora, Kansas.
Business Info:
We are a local cut flower farm located in Eudora, Kansas, founded by Corinne Haldwick. What started as a passion for agriculture and search for more joy in daily life has blossomed into a small business dedicated to providing the community with beautiful, fresh, and sustainable flowers. We specialize in local, seasonal blooms, ensuring that every petal reflects the care and dedication we pour into our craft. Our mission is to deliver the highest quality flowers directly to our customers through local farmers markets and to florists who share our commitment to sustainability. Join us in celebrating the beauty of nature, one bloom at a time!
Contact Details:
Corinne Haldwick
Owner
Phone 913-555-0147
Facebook: Rosalind Thorpe Gardens
Instagram: @RosalindThorpeGardens
Website: RosalindThorpeGardens.example
Target Market(s)
Wholesale to Florists and Direct to Consumer via Farmers Market
Industry/Entity Type
Florist, Farm
Contact Information for Business Card
Name, Contact Info, Logo
Look and feel
Each slider illustrates characteristics of the customer's brand and the style your logo design should communicate.

```html
<!DOCTYPE html>
<html lang="en">
<head>
<meta charset="utf-8">
<title>Rosalind Thorpe Gardens – Business Card</title>
<link href="https://fonts.googleapis.com/css2?family=Montserrat:wght@400;500;700&display=swap" rel="stylesheet">
<style>
  :root {
    --page-bg: #e9eaea;
    --card-white: #ffffff;
    --ink-teal: #0f2b2e;
    --deep-teal: #0a2a2e;
    --deeper-teal: #061b1e;
    --glow-teal: #4fa9b8;
    --mark-white: #ffffff;
  }
  * { box-sizing: border-box; margin: 0; padding: 0; }
  html, body {
    width: 1200px; height: 900px; overflow: hidden;
    background: var(--page-bg);
    font-family: "Montserrat", sans-serif;
  }
  .canvas { position: relative; width: 1200px; height: 900px; }

  .card {
    position: absolute;
    width: 680px; height: 388px;
    border-radius: 38px;
    overflow: hidden;
    box-shadow: 0 14px 30px rgba(0,0,0,0.18);
  }

  /* Back side */
  .card-back {
    left: 150px; top: 46px;
    background: linear-gradient(160deg, var(--deep-teal), var(--deeper-teal));
  }
  .card-back .pattern-field {
    position: absolute; inset: 0;
    background: linear-gradient(125deg, rgba(79,169,184,0.85) 0%, rgba(79,169,184,0.35) 28%, rgba(79,169,184,0.08) 55%, rgba(79,169,184,0) 75%);
  }
  .card-back .back-mark {
    position: absolute; left: 452px; top: 168px;
    color: var(--mark-white);
    font-weight: 500; font-size: 15px; letter-spacing: 1px;
    text-transform: uppercase; line-height: 1.35;
    width: 150px;
  }

  /* Front side */
  .card-front {
    left: 370px; top: 468px;
    background: var(--card-white);
    color: var(--ink-teal);
  }
  .holder { position: absolute; left: 46px; top: 112px; }
  .holder-name { font-weight: 700; font-size: 26px; letter-spacing: 0.3px; }
  .holder-role { font-weight: 400; font-size: 14px; margin-top: 6px; padding-left: 4px; }

  .brand-seal {
    position: absolute; right: 56px; top: 60px;
    width: 236px; height: 236px;
    border: 2px solid var(--ink-teal);
    border-radius: 50%;
    display: flex; align-items: center; justify-content: center;
    text-align: center;
  }
  .brand-name {
    font-weight: 500; font-size: 20px; letter-spacing: 2px;
    text-transform: uppercase; line-height: 1.35;
    color: var(--ink-teal);
  }

  .contact-list {
    position: absolute; left: 48px; bottom: 40px;
    list-style: none;
    font-size: 16px; font-weight: 400;
  }
  .contact-list li { display: flex; align-items: center; gap: 10px; height: 26px; }
  .contact-list svg { width: 16px; height: 16px; flex: none; }
</style>
</head>
<body>
<main class="canvas">

  <section class="card card-back" aria-label="Card back">
    <div class="pattern-field" role="img" aria-label="Repeating brand monogram pattern with a teal sheen"></div>
    <div class="back-mark">Rosalind Thorpe Gardens</div>
  </section>

  <section class="card card-front" aria-label="Card front">
    <div class="holder">
      <h1 class="holder-name">Corinne Haldwick</h1>
      <p class="holder-role">Owner</p>
    </div>

    <div class="brand-seal">
      <span class="brand-name">Rosalind<br>Thorpe<br>Gardens</span>
    </div>

    <ul class="contact-list">
      <li>
        <svg viewBox="0 0 16 16" aria-hidden="true"><path d="M3.5 1.5l2.5 0.5 1 3-1.6 1.2a9 9 0 0 0 4.4 4.4L11 9l3 1 .5 2.5-1.8 1.8C7 14 2 9 1.7 3.3z" fill="var(--ink-teal)"/></svg>
        <span>913-555-0147</span>
      </li>
      <li>
        <svg viewBox="0 0 16 16" aria-hidden="true"><circle cx="8" cy="8" r="7" fill="var(--ink-teal)"/></svg>
        <span>Rosalind Thorpe Gardens</span>
      </li>
      <li>
        <svg viewBox="0 0 16 16" aria-hidden="true"><circle cx="8" cy="8" r="7" fill="var(--ink-teal)"/></svg>
        <span>@RosalindThorpeGardens</span>
      </li>
      <li>
        <svg viewBox="0 0 16 16" aria-hidden="true"><g fill="none" stroke="var(--ink-teal)" stroke-width="1.4"><circle cx="8" cy="8" r="6.5"/><ellipse cx="8" cy="8" rx="3" ry="6.5"/><path d="M1.5 8h13"/></g></svg>
        <span>www.RosalindThorpeGardens.example</span>
      </li>
    </ul>
  </section>

</main>
</body>
</html>
```